established boer goat stud and dorper sheep stud need an updated look

I need a design to promote the boer goat stud and dorper sheep stud, so its clear and simple
Updates

Details for business card design Wirrabel Boers and Dorper Sheep Stud. I would like silhouette animal head or full body of a boer goat (not a dairy breed goat) and Dorper sheep. Contact: Maree Dalton +61 412578304 Sandra Pollock +61 438615027 Mooroopna North Victoria Australia Email: wirrabel5184@mailvane.com

Industry/Entity Type

Agriculture

Contact Information for Business Card

Wirrabel Boers and Dorper Sheep Stud Maree Dalton +61 412578304 Sandra Pollock +61 438615027 wirrabel5184@mailvane.com Kelvale Victoria Australia

Colors
EE7325
F08F49
F5BC92
FAE3D3
FDF4ED

Requirements
Must have
• My Boer Goats and Dorper Sheep images see my photos

```html
<!DOCTYPE html>
<html lang="en">
<head>
<meta charset="utf-8">
<title>Wirrabel Boers and Dorper Sheep Stud – Business Cards</title>
<link href="https://fonts.googleapis.com/css2?family=Bebas+Neue&family=Montserrat:wght@700&family=Lato:wght@400;700&display=swap" rel="stylesheet">
<style>
  :root {
    --orange: #EE7325;
    --orange-soft: #F08F49;
    --ink: #1e1e1e;
    --paper: #ffffff;
    --backdrop: #a9a9a9;
    --grass: #6f8a45;
    --grass-light: #9aa96a;
    --fleece: #efe6d6;
  }
  html, body {
    margin: 0;
    width: 1200px;
    height: 900px;
    overflow: hidden;
    background: var(--backdrop);
  }
  .canvas {
    position: relative;
    width: 1200px;
    height: 900px;
  }
  .card {
    position: absolute;
    left: 260px;
    width: 680px;
    height: 390px;
    border-radius: 24px;
    overflow: hidden;
    background: var(--paper);
  }
  .card--sandra { top: 45px; }
  .card--maree { top: 465px; }
  .card__art {
    position: absolute;
    inset: 0;
  }
  .card__title {
    position: absolute;
    left: 40px;
    top: 30px;
    margin: 0;
    font-family: "Bebas Neue", "Oswald", sans-serif;
    font-weight: 400;
    font-size: 46px;
    letter-spacing: 0.5px;
    color: var(--ink);
    line-height: 1;
    text-transform: uppercase;
  }
  .card__contact {
    position: absolute;
    left: 60px;
    top: 112px;
  }
  .card__name {
    margin: 0;
    font-family: "Montserrat", sans-serif;
    font-weight: 700;
    font-size: 28px;
    color: var(--orange);
    line-height: 1.1;
  }
  .card__phone {
    margin: 4px 0 0;
    font-family: "Lato", sans-serif;
    font-size: 21px;
    letter-spacing: 1px;
    color: var(--ink);
  }
  .card__footer {
    position: absolute;
    left: 60px;
    right: 30px;
    bottom: 14px;
    display: flex;
    align-items: center;
    gap: 26px;
    font-family: "Lato", sans-serif;
    font-weight: 700;
    font-size: 20px;
    color: var(--paper);
  }
  .card__footer-item {
    display: flex;
    align-items: center;
    gap: 8px;
  }
  .card__icon { width: 22px; height: 22px; fill: var(--paper); }
</style>
</head>
<body>
<main class="canvas">

  <article class="card card--sandra">
    <svg class="card__art" viewBox="0 0 680 390" aria-hidden="false">
      <defs>
        <linearGradient id="sheep-field" x1="0" y1="1" x2="1" y2="0">
          <stop offset="0" stop-color="#7d8a4f"/>
          <stop offset="0.45" stop-color="#d9d0bf"/>
          <stop offset="0.75" stop-color="#a7a987"/>
          <stop offset="1" stop-color="#c9b58c"/>
        </linearGradient>
      </defs>
      <path d="M0,282 C170,285 300,245 380,175 C455,110 560,70 680,58" fill="none" stroke="var(--orange)" stroke-width="5"/>
      <path class="card__photo" role="img" aria-label="Photo of Dorper sheep and Boer goats grazing in a paddock"
            d="M0,300 C180,300 305,258 390,185 C460,125 560,85 680,75 L680,390 L0,390 Z" fill="url(#sheep-field)"/>
      <path d="M0,300 C180,300 305,258 390,185 C460,125 560,85 680,75" fill="none" stroke="var(--ink)" stroke-width="6"/>
      <path d="M0,345 L680,335 L680,390 L0,390 Z" fill="var(--orange)"/>
    </svg>
    <h1 class="card__title">Wirrabel Boers and Dorper Sheep Stud</h1>
    <div class="card__contact">
      <p class="card__name">Sandra Pollock</p>
      <p class="card__phone">+61 438615027</p>
    </div>
    <div class="card__footer">
      <span class="card__footer-item">
        <svg class="card__icon" viewBox="0 0 24 24"><path d="M2 5h20v14H2z M3 6l9 7 9-7" fill="none" stroke="#fff" stroke-width="2"/></svg>
        wirrabel5184@mailvane.com
      </span>
      <span class="card__footer-item">
        <svg class="card__icon" viewBox="0 0 24 24"><path d="M12 2a7 7 0 0 0-7 7c0 5 7 13 7 13s7-8 7-13a7 7 0 0 0-7-7zm0 9.5a2.5 2.5 0 1 1 0-5 2.5 2.5 0 0 1 0 5z"/></svg>
        Kelvale Victoria Australia
      </span>
    </div>
  </article>

  <article class="card card--maree">
    <svg class="card__art" viewBox="0 0 680 390" aria-hidden="false">
      <defs>
        <linearGradient id="goat-field" x1="0" y1="1" x2="1" y2="0">
          <stop offset="0" stop-color="#5f7a3a"/>
          <stop offset="0.35" stop-color="#7a4a2c"/>
          <stop offset="0.6" stop-color="#8ea35a"/>
          <stop offset="1" stop-color="#e6dccb"/>
        </linearGradient>
      </defs>
      <path d="M0,282 C170,285 300,245 380,175 C455,110 560,70 680,58" fill="none" stroke="var(--orange)" stroke-width="5"/>
      <path class="card__photo" role="img" aria-label="Photo of Boer goats and Dorper sheep grazing by a fence"
            d="M0,300 C180,300 305,258 390,185 C460,125 560,85 680,75 L680,390 L0,390 Z" fill="url(#goat-field)"/>
      <path d="M0,300 C180,300 305,258 390,185 C460,125 560,85 680,75" fill="none" stroke="var(--ink)" stroke-width="6"/>
      <path d="M0,345 L680,335 L680,390 L0,390 Z" fill="var(--orange)"/>
    </svg>
    <h1 class="card__title">Wirrabel Boers and Dorper Sheep Stud</h1>
    <div class="card__contact">
      <p class="card__name">Maree Dalton</p>
      <p class="card__phone">+61 412578304</p>
    </div>
    <div class="card__footer">
      <span class="card__footer-item">
        <svg class="card__icon" viewBox="0 0 24 24"><path d="M2 5h20v14H2z M3 6l9 7 9-7" fill="none" stroke="#fff" stroke-width="2"/></svg>
        wirrabel5184@mailvane.com
      </span>
      <span class="card__footer-item">
        <svg class="card__icon" viewBox="0 0 24 24"><path d="M12 2a7 7 0 0 0-7 7c0 5 7 13 7 13s7-8 7-13a7 7 0 0 0-7-7zm0 9.5a2.5 2.5 0 1 1 0-5 2.5 2.5 0 0 1 0 5z"/></svg>
        Kelvale Victoria Australia
      </span>
    </div>
  </article>

</main>
</body>
</html>
```